The Visual Personality of Miss Cobbler Food Trailer

Something that stands out with color and our logo. This is a food trailer that attends several events in the spring and summer. We are known for being one of the best Gumbo producers in mid Michigan. We have been responsible for connecting different communities and cultures together and we are strong supporters of our veterans since this is a veteran owned business. All of our vegetables are fresh and locally purchased. These recipes are originally from New Orleans Louisiana. Our website is Misscobbler.net. This will be used for an 8" x 11" poster. Leave a box or area that states "WHERE WE WILL BE:" so that we can add the location of the event that we are attending.

Target Market(s)

We do cuisine that is recognized in the southern states of the USA. but live in the northern part of the USA. We are providing a menu of different southern recipes so they do not have to go all the way down south for get..

Industry/Entity Type

Food/Restaurant Industry

Font styles to use
Serif
Decorative

Colors
0094D4
00A9DD
6FCCEA
C7EBF8
E9F6FB
59FF00
82FF00
B8FF75
E3FFCB
F4FFEA
FFF300
FFF600
FEFA6F
FFFEC7
FFFEE8
EE7325
F08F49
F5BC92
FAE3D3
FDF4ED
EB3D1F
EC4F4E
F09395
F8D3D4
FCEDEE
A7469A
B969AE
D3A5CF
EDDBEB
F8F0F9

Requirements
Must have
• Our logo, which is "Miss Cobbler", "Homemade Deliciousness". We need an area on the poster where we can manually add the location of the event we will be attending because it changes weekly. location
Nice to have
• Bold colors and logo

```html
<!DOCTYPE html>
<html lang="en">
<head>
<meta charset="UTF-8">
<title>Miss Cobbler Food Trailer – Poster</title>
<link href="https://fonts.googleapis.com/css2?family=Fraunces:opsz,wght@9..144,600;9..144,700;9..144,800&family=Josefin+Sans:wght@600;700&family=Montserrat:ital,wght@0,600;0,700;1,500;1,700&display=swap" rel="stylesheet">
<style>
  :root {
    --page: #d9d9d9;
    --wine: #7a2f33;
    --wine-deep: #6a262a;
    --gold: #d4b07a;
    --cream: #f2efea;
    --white: #ffffff;
    --tab: #efeeec;
    --ink: #2a2020;
    --accent-red: #eb3d1f;
  }
  * { margin: 0; padding: 0; box-sizing: border-box; }
  html, body { width: 1200px; height: 1200px; overflow: hidden; background: var(--page); }
  .poster {
    position: absolute; left: 164px; top: 30px;
    width: 872px; height: 1140px;
    background: linear-gradient(160deg, var(--wine) 0%, var(--wine-deep) 55%, var(--wine) 100%);
    overflow: hidden;
  }
  .brand-tab { position: absolute; left: 46px; top: 0; width: 229px; height: 240px; }
  .brand-name {
    position: absolute; left: 46px; top: 70px; width: 229px; text-align: center;
    font-family: "Fraunces", serif; font-weight: 700; font-size: 30px; line-height: 1.05; color: var(--wine);
  }
  .brand-dot { display: block; width: 22px; height: 22px; border-radius: 50%; background: var(--accent-red); margin: 0 auto 8px; }
  .brand-tagline {
    position: absolute; left: 46px; top: 160px; width: 229px; text-align: center;
    font-family: "Montserrat", sans-serif; font-weight: 700; font-size: 9px; letter-spacing: .5px; color: var(--ink);
  }
  .headline { position: absolute; left: 308px; top: 0; width: 524px; height: 220px; }
  .headline svg { display: block; width: 524px; height: 220px; }
  .headline text { font-family: "Josefin Sans", sans-serif; fill: var(--cream); }
  .headline .big { font-size: 96px; font-weight: 700; }
  .headline .sub { font-size: 64px; font-weight: 600; }

  .pitch { position: absolute; left: 51px; width: 356px; text-align: center; font-family: "Fraunces", serif; font-weight: 800; color: var(--gold); line-height: 1; white-space: nowrap; }
  .pitch .white { color: var(--cream); }
  .l1 { top: 300px; font-size: 58px; }
  .l2 { top: 366px; font-size: 56px; }
  .l3 { top: 422px; font-size: 62px; }
  .l4 { top: 480px; font-size: 30px; }
  .l5 { top: 512px; font-size: 37px; }
  .l6 { top: 580px; font-size: 35px; }
  .l7 { top: 634px; font-size: 50px; color: var(--cream); }
  .l8 { top: 736px; font-size: 30px; }
  .l9 { top: 766px; font-size: 56px; letter-spacing: 2px; }
  .rule { position: absolute; height: 2px; background: var(--gold); }
  .banner { position: absolute; left: 51px; top: 625px; width: 356px; height: 78px; }

  .where { position: absolute; left: 51px; top: 836px; width: 356px; text-align: center; font-family: "Montserrat", sans-serif; font-style: italic; font-weight: 700; font-size: 15px; color: var(--white); }
  .location-box { position: absolute; left: 52px; top: 865px; width: 354px; height: 46px; border-radius: 6px; background: linear-gradient(180deg, #f4f4f4, #dcdcdc); }

  .info { position: absolute; left: 51px; width: 356px; text-align: center; font-family: "Montserrat", sans-serif; color: var(--white); }
  .info-label { font-style: italic; font-weight: 500; font-size: 14px; }
  .contact-row { top: 966px; display: flex; justify-content: center; align-items: center; gap: 10px; font-weight: 700; font-size: 14px; }
  .contact-row .divider { width: 1px; height: 42px; background: var(--cream); margin: 0 4px; }
  .icon-box { width: 20px; height: 20px; border-radius: 3px; background: var(--gold); display: inline-flex; align-items: center; justify-content: center; }
  .social-row { top: 1044px; display: flex; justify-content: center; align-items: center; gap: 16px; }
  .social-square { width: 34px; height: 34px; border: 2px solid var(--gold); border-radius: 7px; }
  .social-row .divider { width: 1px; height: 40px; background: var(--cream); }
  .handle { top: 1098px; font-weight: 700; font-size: 16px; color: var(--gold); }

  .dish { position: absolute; }
  .dish-label {
    position: absolute; width: 112px; height: 112px; border-radius: 50%;
    background: rgba(240, 232, 232, .82);
    display: flex; align-items: center; justify-content: center; text-align: center;
    font-family: "Fraunces", serif; font-weight: 700; font-size: 22px; line-height: 1; color: var(--ink);
  }
</style>
</head>
<body>
<main class="poster">
  <svg class="brand-tab" viewBox="0 0 229 240" aria-hidden="true">
    <path d="M0 0 H229 V212 Q229 232 209 230 Q114 214 20 230 Q0 232 0 212 Z" fill="var(--tab)"/>
  </svg>
  <div class="brand-name"><span class="brand-dot"></span>Miss<br>Cobbler</div>
  <div class="brand-tagline">HOMEMADE DELICIOUSNESS!</div>

  <h1 class="headline">
    <svg viewBox="0 0 524 220">
      <text class="big" x="4" y="128" textLength="512" lengthAdjust="spacingAndGlyphs">HOMEMADE</text>
      <text class="sub" x="6" y="193" textLength="512" lengthAdjust="spacingAndGlyphs">DELICIOUSNESS</text>
    </svg>
  </h1>

  <p class="pitch l1">All of our</p>
  <p class="pitch l2">vegetables</p>
  <p class="pitch l3">are <span class="white">Fresh</span></p>
  <span class="rule" style="left:51px;top:496px;width:128px"></span>
  <span class="rule" style="left:279px;top:496px;width:128px"></span>
  <p class="pitch l4">and</p>
  <p class="pitch l5">locally purchased</p>
  <span class="rule" style="left:51px;top:566px;width:356px"></span>
  <p class="pitch l6">with recipes that</p>
  <svg class="banner" viewBox="0 0 356 78" aria-hidden="true">
    <polygon points="12,2 344,2 326,39 352,76 4,76 30,39" fill="none" stroke="var(--gold)" stroke-width="3"/>
  </svg>
  <p class="pitch l7">Originated</p>
  <span class="rule" style="left:51px;top:752px;width:128px"></span>
  <span class="rule" style="left:279px;top:752px;width:128px"></span>
  <p class="pitch l8">from</p>
  <p class="pitch l9">Louisiana</p>

  <p class="where">WHERE WE WILL BE !</p>
  <div class="location-box" aria-label="Space for event location"></div>

  <p class="info info-label" style="top:934px">Information:</p>
  <div class="info contact-row">
    <span>Misscobbler.net</span>
    <span class="icon-box"><svg width="12" height="12" viewBox="0 0 12 12"><path d="M2 1 L11 6 L6 7 L4 11 Z" fill="var(--wine)"/></svg></span>
    <span class="divider"></span>
    <span class="icon-box"><svg width="12" height="12" viewBox="0 0 24 24"><path d="M6.6 10.8a15 15 0 0 0 6.6 6.6l2.2-2.2a1 1 0 0 1 1-.25 11.4 11.4 0 0 0 3.6.6 1 1 0 0 1 1 1V20a1 1 0 0 1-1 1A17 17 0 0 1 3 4a1 1 0 0 1 1-1h3.5a1 1 0 0 1 1 1c0 1.25.2 2.45.6 3.6a1 1 0 0 1-.25 1z" fill="var(--wine)"/></svg></span>
    <span>555-0142-7788</span>
  </div>
  <p class="info info-label" style="top:1020px">Follow us on:</p>
  <div class="info social-row">
    <span class="social-square"></span>
    <span class="divider"></span>
    <span class="social-square"></span>
  </div>
  <p class="info handle">misscobbler</p>

  <svg class="dish" style="left:503px;top:241px" width="369" height="298" viewBox="0 0 369 298" role="img" aria-label="Photo of a shrimp and tomato flatbread pizza">
    <defs><radialGradient id="pizzaTone" cx="50%" cy="50%" r="60%"><stop offset="0" stop-color="#e8c48c"/><stop offset="1" stop-color="#d9c89a"/></radialGradient></defs>
    <path d="M20 30 Q180 -10 369 0 V298 Q200 300 90 250 Q0 200 0 120 Q0 50 20 30 Z" fill="url(#pizzaTone)"/>
  </svg>
  <svg class="dish" style="left:514px;top:515px" width="358" height="340" viewBox="0 0 358 340" role="img" aria-label="Photo of a bowl of chicken gumbo">
    <defs><radialGradient id="gumboTone" cx="55%" cy="50%" r="55%"><stop offset="0" stop-color="#c4604a"/><stop offset=".8" stop-color="#b86a4e"/><stop offset="1" stop-color="#ece9e4"/></radialGradient></defs>
    <ellipse cx="200" cy="170" rx="200" ry="170" fill="url(#gumboTone)"/>
  </svg>
  <svg class="dish" style="left:524px;top:831px" width="348" height="306" viewBox="0 0 348 306" role="img" aria-label="Photo of a shrimp po boy sandwich">
    <defs><linearGradient id="poboyTone" x1="0" y1="0" x2="0" y2="1"><stop offset="0" stop-color="#c98a52"/><stop offset=".45" stop-color="#d9b9a0"/><stop offset="1" stop-color="#b9703f"/></linearGradient></defs>
    <path d="M10 120 Q40 10 200 0 Q320 -5 348 10 V260 Q200 300 60 270 Q0 250 10 120 Z" fill="url(#poboyTone)"/>
  </svg>

  <div class="dish-label" style="left:477px;top:275px">Pizza</div>
  <div class="dish-label" style="left:477px;top:618px">Chicken<br>Gumbo</div>
  <div class="dish-label" style="left:477px;top:978px">Shrimp<br>Po Boy</div>
</main>
</body>
</html>
```